Logo, Web and Mobile Designs for enterprise social media platform

All the details are in the attached document, please start reading the scope document first which explains what is this project about and the details about the needed deliverables, after that please read the UI_Requirements document which will detail what is expected regarding the coded web version since this is a coded contest, it is very important that you meet the UI requirements or suggest something else but we will need to agree first before working on the coded version

Good Luck

Target Market(s)

Enterprise Social Media

Industry/Entity Type

Media

Coding

Coded - Design and coding required

Number of Pages Required

5+ page

Font styles to use
Sans Serif

Requirements
Must have
• All the must haves are listed in the scope document so please check before you start

```html
<!DOCTYPE html>
<html lang="en">
<head>
<meta charset="utf-8">
<title>Crewline — Sign in</title>
<link rel="stylesheet" href="https://fonts.googleapis.com/css2?family=Roboto:wght@300;400;500&display=swap">
<style>
  :root {
    --brand-blue: #64b5f6;
    --white: #ffffff;
    --field-border: #a8a8a8;
    --placeholder: #bdbdbd;
    --ink: #424242;
  }
  * { box-sizing: border-box; margin: 0; padding: 0; }
  html, body {
    width: 1200px;
    height: 750px;
    overflow: hidden;
    background: var(--white);
    font-family: "Roboto", Arial, sans-serif;
  }
  .app-bar {
    position: absolute;
    left: 0; top: 0;
    width: 1200px;
    height: 83px;
    background: var(--brand-blue);
    box-shadow: 0 1px 3px rgba(0,0,0,0.25);
    display: flex;
    align-items: center;
    justify-content: center;
  }
  .app-bar__name {
    color: var(--white);
    font-weight: 400;
    font-size: 55px;
    letter-spacing: 1px;
    line-height: 1;
    padding-top: 2px;
  }
  .login-form {
    position: absolute;
    left: 460px;
    top: 328px;
    width: 280px;
  }
  .login-form__field {
    display: block;
    width: 280px;
    height: 51px;
    border: 1px solid var(--field-border);
    border-radius: 2px;
    box-shadow: 0 1px 2px rgba(0,0,0,0.18);
    padding: 0 17px;
    font-family: inherit;
    font-size: 21px;
    font-weight: 300;
    color: var(--ink);
    background: var(--white);
    outline: none;
  }
  .login-form__field::placeholder { color: var(--placeholder); }
  .login-form__field + .login-form__field { margin-top: 11px; }
  .login-form__actions {
    margin-top: 13px;
    display: flex;
    justify-content: space-between;
    align-items: center;
  }
  .button {
    height: 50px;
    border: none;
    font-family: inherit;
    font-size: 20px;
    text-transform: uppercase;
    cursor: pointer;
  }
  .button--flat {
    width: 130px;
    background: transparent;
    color: var(--brand-blue);
    font-weight: 400;
  }
  .button--raised {
    width: 136px;
    background: var(--brand-blue);
    color: var(--white);
    font-weight: 500;
  }
</style>
</head>
<body>
  <header class="app-bar">
    <h1 class="app-bar__name">CREWLINE</h1>
  </header>

  <form class="login-form">
    <input class="login-form__field" type="text" placeholder="username or e-mail">
    <input class="login-form__field" type="password" placeholder="password">
    <div class="login-form__actions">
      <button class="button button--flat" type="submit">Login</button>
      <button class="button button--raised" type="button">Sign up</button>
    </div>
  </form>
</body>
</html>
```